K SPIRES Business Card Design

Need a business card design for K Spires, we're a tower company - our main scope of work is to upgrade cellular sites: swap antennas, install new coax, fiber, replace mounts, etc. Mostly tower work.

would like to see a sharp business card design with our logo either on background or with tower image on the background - something describing our field not only in words but in images.

Target Market(s)

USA

Industry/Entity Type

Business

Contact Information for Business Card

Tarnek Obliva
Operations Manager
K Spires LLC

cell 555-318-2094
tarnek@k-spires-example.com

4185 Wexbridge Commerce Pkwy, Suite D
Norcross, GA, 30571

Requirements
Must have
• some tower related design
Nice to have
• some tower or cellular antennas on the background, if possible to compliment our logo...

```html
<!DOCTYPE html>
<html lang="en">
<head>
<meta charset="utf-8">
<title>K Spires Business Card</title>
<link href="https://fonts.googleapis.com/css2?family=Alegreya:wght@400;700&display=swap" rel="stylesheet">
<style>
  :root {
    --page-bg: #2b2724;
    --card-bg: #141414;
    --card-back-bg: #0d0d0d;
    --silver: #d9d9d9;
    --silver-dim: #8f8f8f;
    --text-light: #ececec;
    --divider: #5a5a5a;
    --back-logo: #4a4a4a;
  }
  * { margin: 0; padding: 0; box-sizing: border-box; }
  html, body { width: 1200px; height: 844px; overflow: hidden; }
  body {
    background: var(--page-bg);
    font-family: "Alegreya", Georgia, serif;
    position: relative;
  }
  .card {
    position: absolute;
    top: 267px;
    width: 540px;
    height: 310px;
    box-shadow: 0 10px 30px rgba(0,0,0,.45);
  }
  .card-front { left: 40px; background: var(--card-bg); }
  .card-back { left: 620px; background: var(--card-back-bg); }

  .front-logo {
    position: absolute;
    left: 0; right: 0; top: 46px;
    text-align: center;
    font-size: 46px;
    font-weight: 400;
    color: var(--silver);
    letter-spacing: 1px;
  }
  .identity {
    position: absolute;
    right: 290px;
    top: 166px;
    width: 240px;
    text-align: right;
  }
  .identity .name { font-size: 22px; font-weight: 700; color: var(--text-light); line-height: 1.2; }
  .identity .role { font-size: 15px; color: var(--silver-dim); line-height: 1.2; }
  .identity .address { font-size: 14px; color: var(--text-light); margin-top: 12px; line-height: 1.35; }
  .divider {
    position: absolute;
    left: 264px; top: 160px;
    width: 1px; height: 120px;
    background: var(--divider);
  }
  .contacts {
    position: absolute;
    left: 280px; top: 160px;
    list-style: none;
    font-size: 14px;
    color: var(--text-light);
    line-height: 22px;
    white-space: nowrap;
  }
  .contacts li { display: flex; align-items: center; gap: 8px; }
  .contacts svg { width: 11px; height: 11px; fill: var(--text-light); flex: none; }

  .tower-art {
    position: absolute;
    left: 110px; top: 40px;
    width: 70px; height: 250px;
    background: linear-gradient(180deg, #1c1c1c, #111);
  }
  .back-logo {
    position: absolute;
    left: 150px; top: 72px;
    font-size: 78px;
    font-weight: 400;
    color: var(--back-logo);
    letter-spacing: 1px;
  }
</style>
</head>
<body>
  <section class="card card-front">
    <div class="front-logo">K Spires</div>

    <div class="identity">
      <div class="name">Tarnek Obliva</div>
      <div class="role">Operations Manager</div>
      <div class="address">4185 Wexbridge Commerce Pkwy,<br>Suite D, Norcross, GA, 30571</div>
    </div>

    <div class="divider"></div>

    <ul class="contacts">
      <li><svg viewBox="0 0 12 12"><path d="M2 1h3l1 3-1.5 1a6 6 0 0 0 2.5 2.5L8 6l3 1v3a1 1 0 0 1-1 1A9 9 0 0 1 1 2a1 1 0 0 1 1-1z"/></svg>555-318-2094</li>
      <li><svg viewBox="0 0 12 12"><rect x="1" y="4" width="10" height="7" rx="1"/><rect x="3" y="1" width="6" height="3"/></svg>555-318-2095</li>
      <li><svg viewBox="0 0 12 12"><rect x="3" y="0.5" width="6" height="11" rx="1"/></svg>555-318-2096</li>
      <li><svg viewBox="0 0 12 12"><path d="M1 2.5h10v7H1z"/></svg>tarnek@k-spires-example.com</li>
      <li><svg viewBox="0 0 12 12"><path d="M4 8l4-4M3 6L1.5 7.5a2 2 0 0 0 3 3L6 9M6 3l1.5-1.5a2 2 0 0 1 3 3L9 6" stroke="#ececec" stroke-width="1.4" fill="none"/></svg>www.k-spires-example.com</li>
    </ul>
  </section>

  <section class="card card-back">
    <div class="tower-art" role="img" aria-label="Line illustration of a lattice cell tower"></div>
    <div class="back-logo">K Spires</div>
  </section>
</body>
</html>
```